High-end construction company needs a business card design

We need a modern looking business card that draws people in, is memorable and looks so good people will want to sick it on their fridges.
On the first side what is needed are:
Logo
My name - Tomasz Brelwik
Title - Managing Director
Website - www.varkelt.co.uk
Email - tomasz@varkelt.co.uk
Telephone - 020 5194 6281
Mobile - 07845139072
On the back side was is needed is a list of all the services we provide:
-Kitchen Renovations
-Bathroom Renovations
-House Renovations
-Garage Conversions
-Extensions
-Loft Conversions
-Conservatories
-Carpentry
-Tiling
-Electrical
-Plumbing & Heating
-Bricklaying
-Landscaping
-Decorating
-Plastering
We would like the colours to be the same shades as on the logo with grey or black for the words.
Target Market(s)
Anyone who needs building work done
Contact Information for Business Card
This business card is for a construction company which strives to deliver excellent service and quality.
The look and feel of the card should represent this.
Requirements
Must have
- On the first side what is needed are:
Logo
My name - Tomasz Brelwik
Title - Managing Director
Website - www.varkelt.co.uk
Email - tomasz@varkelt.co.uk
Telephone - 020 5194 6281
Mobile - 07845139072
Nice to have
- Cool looking features

```html
<!DOCTYPE html>
<html lang="en">
<head>
<meta charset="utf-8">
<title>Varkelt Construction Ltd – Business Card</title>
<link rel="stylesheet" href="https://fonts.googleapis.com/css2?family=Exo+2:wght@400;500;600;800&display=swap">
<style>
  :root {
    --green-dark: #3f8a37;
    --green: #55a043;
    --green-bright: #7cc242;
    --ink-grey: #6b6b6b;
    --paper: #ffffff;
    --backdrop: #2a2a2a;
    --font-main: "Exo 2", "Segoe UI", sans-serif;
  }
  * { box-sizing: border-box; margin: 0; padding: 0; }
  html, body {
    width: 1200px; height: 880px; overflow: hidden;
    background: var(--backdrop);
    font-family: var(--font-main);
  }
  .stage { position: relative; width: 1200px; height: 880px; }

  .card {
    position: absolute;
    width: 595px; height: 340px;
    border-radius: 18px;
    background: var(--paper);
    overflow: hidden;
    box-shadow: 0 18px 40px rgba(0,0,0,.45);
  }

  /* ---------- services side ---------- */
  .card-services { left: 60px; top: 70px; }
  .services-body {
    position: absolute; inset: 0;
    display: flex; flex-direction: column; align-items: center; justify-content: center;
    text-align: center; padding: 0 30px;
  }
  .services-title {
    font-weight: 800; font-size: 22px; letter-spacing: 1px;
    color: var(--green-dark);
    margin-bottom: 10px;
  }
  .services-list {
    list-style: none;
    font-size: 15px; line-height: 1.55; color: var(--ink-grey);
    font-weight: 500; letter-spacing: .5px;
  }
  .services-site {
    margin-top: 22px;
    font-size: 14px; letter-spacing: 6px; font-weight: 600;
    color: var(--green);
  }

  /* ---------- contact side ---------- */
  .card-contact { left: 545px; top: 470px; }
  .contact-bg { position: absolute; inset: 0; width: 100%; height: 100%; }
  .brand {
    position: absolute; left: 40px; top: 125px;
    color: var(--green); font-weight: 800;
  }
  .brand-row { display: flex; align-items: center; gap: 10px; }
  .brand-mark { width: 24px; height: 24px; background: var(--green); }
  .brand-name { font-size: 46px; letter-spacing: 2px; line-height: 1; }
  .brand-sub { font-size: 15px; letter-spacing: 3px; margin-top: 6px; }

  .person {
    position: absolute; left: 392px; top: 68px;
    color: var(--paper);
  }
  .person-name { font-weight: 800; font-size: 19px; letter-spacing: .5px; text-transform: uppercase; line-height: 1.2; }
  .person-title { font-size: 13px; font-weight: 500; letter-spacing: .5px; }

  .contact-list {
    position: absolute; left: 392px; top: 168px;
    list-style: none; color: var(--paper);
    font-size: 14px; font-weight: 500;
  }
  .contact-item { display: flex; align-items: center; gap: 9px; margin-bottom: 8px; }
  .contact-icon { width: 17px; height: 17px; flex: none; }
</style>
</head>
<body>
<main class="stage">

  <section class="card card-services" aria-label="Services side">
    <div class="services-body">
      <h2 class="services-title">OUR SERVICES</h2>
      <ul class="services-list">
        <li>Kitchen Renovations | Bathroom Renovations | House Renovations</li>
        <li>Garage Conversions | Extensions | Loft Conversions | Conservatories</li>
        <li>Carpentry | Tiling | Electrical | Plumbing &amp; Heating | Bricklaying</li>
        <li>Landscaping | Decorating | Plastering</li>
      </ul>
      <p class="services-site">www.varkelt.co.uk</p>
    </div>
  </section>

  <section class="card card-contact" aria-label="Contact side">
    <svg class="contact-bg" viewBox="0 0 595 340" preserveAspectRatio="none" aria-hidden="true">
      <defs>
        <linearGradient id="greenPanel" x1="0" y1="0" x2="1" y2="1">
          <stop offset="0" stop-color="#4a9440"/>
          <stop offset="1" stop-color="#5ea84a"/>
        </linearGradient>
      </defs>
      <path d="M310,40 C390,120 382,250 308,340 L595,340 L595,0 Z" fill="#7cc242"/>
      <path d="M290,0 C370,60 380,220 332,340 L595,340 L595,0 Z" fill="url(#greenPanel)"/>
    </svg>

    <div class="brand">
      <div class="brand-row">
        <span class="brand-mark" aria-hidden="true"></span>
        <span class="brand-name">VARKELT</span>
      </div>
      <div class="brand-sub">CONSTRUCTION LTD</div>
    </div>

    <div class="person">
      <h1 class="person-name">Tomasz Brelwik</h1>
      <p class="person-title">Managing Director</p>
    </div>

    <ul class="contact-list">
      <li class="contact-item">
        <svg class="contact-icon" viewBox="0 0 20 20" aria-hidden="true"><circle cx="10" cy="10" r="9" fill="#fff"/><path d="M7 5.5l2 2-1 1.2c.6 1.3 1.6 2.3 2.9 2.9l1.2-1 2 2-1.3 1.4c-3.3-.4-6.5-3.6-6.9-6.9z" fill="#4a9440"/></svg>
        <span>020 5194 6281</span>
      </li>
      <li class="contact-item">
        <svg class="contact-icon" viewBox="0 0 20 20" aria-hidden="true"><circle cx="10" cy="10" r="9" fill="#fff"/><rect x="7" y="4.5" width="6" height="11" rx="1" fill="#4a9440"/><rect x="8" y="6" width="4" height="7" fill="#fff"/></svg>
        <span>07845139072</span>
      </li>
      <li class="contact-item">
        <svg class="contact-icon" viewBox="0 0 20 20" aria-hidden="true"><circle cx="10" cy="10" r="9" fill="#fff"/><rect x="5" y="6.5" width="10" height="7" fill="#4a9440"/><path d="M5 6.5l5 4 5-4" stroke="#fff" stroke-width="1" fill="none"/></svg>
        <span>tomasz@varkelt.co.uk</span>
      </li>
      <li class="contact-item">
        <svg class="contact-icon" viewBox="0 0 20 20" aria-hidden="true"><circle cx="10" cy="10" r="9" fill="#fff"/><circle cx="10" cy="10" r="5" fill="none" stroke="#4a9440" stroke-width="1.3"/><path d="M5 10h10M10 5c-2 3-2 7 0 10M10 5c2 3 2 7 0 10" stroke="#4a9440" stroke-width="1" fill="none"/></svg>
        <span>www.varkelt.co.uk</span>
      </li>
    </ul>
  </section>

</main>
</body>
</html>
```